Brindle Haven Website design in word press

Develop great looking website home page with basic menus in Word Press. We already have a logo, so no need to re-invent that.

Target Market(s)

donors, animal owners, emergency services.

Number of Pages Required

1 page

Font styles to use
Sans Serif

Colors
ec1f27
000000
ffffff
959595

Requirements
Must have
• Fresh design in Word Press, neutral (i.e. not American looking), uses red, black and white as core colours. Needs to have menu options for about us, join us, help us, FAQs, contact us etc. Looking for a smart, modern, professional looking home page, that we can easily add pages/menu's/widgets to. Include social media buttons for facebook, twitter etc.
Nice to have
• Images (could be in colour shades) of animals in disaster i.e. search royalty free Hurricane Lorimel, Hurrican Odwin.
Should not have
• Images that breach copyright.

```html
<!DOCTYPE html>
<html lang="en">
<head>
<meta charset="utf-8">
<title>Brindle Haven</title>
<link rel="stylesheet" href="https://fonts.googleapis.com/css2?family=Montserrat:wght@400;500;600;700&family=Open+Sans:wght@400;600&display=swap">
<style>
:root{
  --red:#ec1f27;
  --black:#000000;
  --white:#ffffff;
  --grey:#959595;
  --text:#333333;
  --light:#f2f2f2;
  --footer:#222222;
}
*{box-sizing:border-box;margin:0;padding:0}
html,body{width:1200px;height:3237px;overflow:hidden;background:var(--white)}
body{position:relative;font-family:"Open Sans",Arial,sans-serif;color:var(--text)}
.abs{position:absolute}
.head{font-family:"Montserrat",Arial,sans-serif}

/* header */
.site-header{left:0;top:0;width:1200px;height:123px;background:var(--white)}
.brand{left:99px;top:22px;display:flex;align-items:center;gap:14px}
.brand-mark{width:80px;height:80px;border-radius:50%;background:var(--red)}
.brand-name{font-family:"Montserrat",Arial,sans-serif;font-weight:700;font-size:17px;color:var(--red);letter-spacing:.5px}
.social{left:668px;top:16px;display:flex;gap:12px}
.social span{width:42px;height:42px;border:2px solid #444;border-radius:50%;display:block}
.search{left:885px;top:20px;width:216px;height:36px;border:1px solid #ccc;font-size:13px;color:#555;padding:8px 10px}
.search svg{position:absolute;right:10px;top:10px}
.main-nav{right:100px;top:86px;display:flex;gap:33px;font-family:"Montserrat",Arial,sans-serif;font-weight:600;font-size:15px;color:var(--black)}
.main-nav .active{color:var(--red)}

/* hero */
.hero{left:0;top:123px;width:1200px;height:516px;background:linear-gradient(100deg,#3d4a4e 0%,#6a6e66 40%,#8a7c66 60%,#4c5452 100%)}
.hero-title{left:99px;top:240px;font-family:"Montserrat",Arial,sans-serif;font-weight:700;font-size:50px;color:var(--white)}
.hero-sub{left:99px;top:318px;width:520px;font-family:"Montserrat",Arial,sans-serif;font-weight:600;font-size:15px;line-height:25px;color:var(--white)}
.btn-outline{left:99px;top:395px;width:118px;height:47px;border:2px solid var(--white);color:var(--white);font-family:"Montserrat",Arial,sans-serif;font-weight:600;font-size:14px;line-height:43px;text-align:center}
.dots{left:99px;top:478px;display:flex;gap:5px}
.dots span{width:14px;height:14px;border-radius:50%;background:rgba(255,255,255,.6)}
.dots span:first-child{background:var(--white)}

/* vision */
.vision-frame{left:99px;top:719px;width:441px;height:360px;background:var(--red)}
.vision-tag{left:99px;top:719px;width:70px;height:360px;display:flex;align-items:center;justify-content:center}
.vision-tag span{transform:rotate(-90deg);white-space:nowrap;font-family:"Montserrat",Arial,sans-serif;font-weight:700;font-size:30px;color:var(--white);letter-spacing:1px}
.vision-photo{left:168px;top:753px;width:425px;height:291px;background:linear-gradient(160deg,#9ca3a6 0%,#6f7678 50%,#50585a 100%)}
.section-title{font-family:"Montserrat",Arial,sans-serif;font-weight:600;font-size:32px;color:var(--red)}
.rule{height:2px;background:var(--red)}
.vision-list{left:641px;top:786px;width:460px;list-style:none;font-size:15.5px;line-height:23px;color:var(--text)}
.vision-list li{position:relative;padding-left:26px;margin-bottom:12px}
.pointer{position:absolute;left:0;top:6px}
.btn-red{background:var(--red);color:var(--white);font-family:"Montserrat",Arial,sans-serif;font-weight:600;font-size:14px;text-align:center}

/* preparedness */
.prep{left:0;top:1167px;width:1200px;height:560px;background:var(--light)}
.slide{top:1316px;height:335px}
.slide-a{left:0;width:399px;background:linear-gradient(140deg,#2f3a2a,#6a6a4c 60%,#3a3a30)}
.slide-b{left:399px;width:399px;background:linear-gradient(140deg,#8d8a84,#5f5a55)}
.slide-c{left:798px;width:402px;background:linear-gradient(140deg,#6a5a48,#8c7c6a 50%,#3e3a34)}
.overlay{left:399px;top:1316px;width:399px;height:335px;background:rgba(236,31,39,.85)}
.overlay-frame{left:405px;top:1322px;width:387px;height:323px;border:2px solid rgba(255,255,255,.8)}
.overlay-title{left:399px;top:1430px;width:399px;text-align:center;font-family:"Montserrat",Arial,sans-serif;font-weight:500;font-size:24px;color:var(--white)}
.overlay-text{left:444px;top:1482px;width:309px;text-align:center;font-size:14px;line-height:22px;color:var(--white)}

/* what we do */
.tile{height:213px}
.tile-img-1{background:linear-gradient(150deg,#7f8fa6,#5b554c 60%,#3c3630)}
.tile-img-2{background:linear-gradient(160deg,#a9b8c8,#8e8a80 50%,#6c6658)}
.tile-img-3{background:linear-gradient(160deg,#c9c6bd,#8f8573 55%,#6b624f)}
.tile-img-4{background:linear-gradient(160deg,#b3bcc4,#898a86 55%,#5f5d56)}
.tile-text{background:var(--white);border:1px solid #e6e6e6;text-align:center;padding:34px 22px 0}
.tile-text h3{font-family:"Montserrat",Arial,sans-serif;font-weight:600;font-size:22px;line-height:28px;color:var(--red);margin-bottom:16px}
.tile-text p{font-size:14.5px;line-height:23px;color:var(--text)}
.notch{position:absolute;top:90px;width:0;height:0;border-top:14px solid transparent;border-bottom:14px solid transparent}
.notch-left{left:-14px;border-right:14px solid var(--white)}
.notch-right{right:-14px;border-left:14px solid var(--white)}

/* how */
.how-list{left:99px;top:2524px;list-style:none;font-size:15.5px;color:var(--text)}
.how-list li{position:relative;padding-left:26px;height:29px;line-height:29px}
.how-list .pointer{top:10px}
.how-art{left:786px;top:2422px;width:310px;height:310px;border-radius:50%;border:3px solid var(--red);background:radial-gradient(circle at 50% 35%,#ffffff 0%,#e9f2f6 50%,#9fd3dc 100%);overflow:hidden}

/* footer */
.site-footer{left:0;top:2816px;width:1200px;height:421px;background:var(--footer)}
.foot-brand{left:99px;top:2942px;display:flex;align-items:center;gap:16px}
.foot-mark{width:120px;height:120px;border-radius:50%;border:4px solid var(--white)}
.foot-name{font-family:"Montserrat",Arial,sans-serif;font-weight:700;font-size:17px;color:var(--white)}
.foot-head{font-family:"Montserrat",Arial,sans-serif;font-weight:700;font-size:22px;color:var(--white)}
.foot-rule{height:2px;width:70px;background:var(--white)}
.foot-links{list-style:none;font-size:14px;color:var(--white)}
.foot-links li{height:30px;line-height:30px;padding-left:26px;position:relative}
.foot-links svg{position:absolute;left:0;top:9px}
.foot-line{left:99px;top:3151px;width:1002px;height:1px;background:#555}
.copyright{left:0;top:3184px;width:1200px;text-align:center;font-size:14px;color:var(--white)}
</style>
</head>
<body>

<header class="abs site-header">
  <div class="abs brand"><span class="brand-mark"></span><span class="brand-name">BRINDLE HAVEN.NZ</span></div>
  <div class="abs social" aria-label="Social links"><span></span><span></span><span></span><span></span></div>
  <div class="abs search">Search...
    <svg width="16" height="16" viewBox="0 0 16 16"><circle cx="6.5" cy="6.5" r="5" fill="none" stroke="#444" stroke-width="2"/><line x1="10" y1="10" x2="15" y2="15" stroke="#444" stroke-width="2"/></svg>
  </div>
  <nav class="abs main-nav">
    <span class="active">HOME</span><span>ABOUT US</span><span>JOIN US</span><span>HELP US</span><span>FAQS</span><span>CONTACT US</span>
  </nav>
</header>

<section>
  <div class="abs hero" role="img" aria-label="Rescuers wading through floodwater leading a dog to safety"></div>
  <h1 class="abs hero-title">BRINDLE HAVEN</h1>
  <p class="abs hero-sub">As we receive no government funding, Brindle Haven needs your help so that animals are not left behind in emergencies.</p>
  <div class="abs btn-outline">READ MORE</div>
  <div class="abs dots"><span></span><span></span><span></span><span></span><span></span></div>
</section>

<section>
  <div class="abs vision-frame"></div>
  <div class="abs vision-tag"><span>BRINDLE HAVEN</span></div>
  <div class="abs vision-photo" role="img" aria-label="People carrying pets through a flooded street in heavy rain"></div>
  <h2 class="abs section-title" style="left:641px;top:706px">Vision: Our Hope</h2>
  <div class="abs rule" style="left:641px;top:755px;width:194px"></div>
  <ul class="abs vision-list">
    <li><svg class="pointer" width="16" height="12" viewBox="0 0 16 12"><path d="M1 6h12M9 2l4 4-4 4" fill="none" stroke="#ec1f27" stroke-width="2"/></svg>An animal-inclusive and disaster resilient New Zealand. Purpose: Why Brindle Haven New Zealand</li>
    <li><svg class="pointer" width="16" height="12" viewBox="0 0 16 12"><path d="M1 6h12M9 2l4 4-4 4" fill="none" stroke="#ec1f27" stroke-width="2"/></svg>To address the significant animal welfare emergency management capability gap</li>
    <li><svg class="pointer" width="16" height="12" viewBox="0 0 16 12"><path d="M1 6h12M9 2l4 4-4 4" fill="none" stroke="#ec1f27" stroke-width="2"/></svg>An animal-inclusive and disaster resilient New Zealand. Purpose: Why Brindle Haven New Zealand</li>
    <li><svg class="pointer" width="16" height="12" viewBox="0 0 16 12"><path d="M1 6h12M9 2l4 4-4 4" fill="none" stroke="#ec1f27" stroke-width="2"/></svg>To protect disaster affected animals in partnership with the community</li>
  </ul>
  <div class="abs btn-red" style="left:667px;top:1036px;width:119px;height:47px;line-height:47px">READ MORE</div>
</section>

<section>
  <div class="abs prep"></div>
  <h2 class="abs section-title" style="left:0;top:1214px;width:1200px;text-align:center;font-size:29px">Emergency Preparedness</h2>
  <div class="abs rule" style="left:552px;top:1272px;width:96px"></div>
  <div class="abs slide slide-a" role="img" aria-label="Volunteer comforting a dog beside floodwater"></div>
  <div class="abs slide slide-b" role="img" aria-label="Rescue worker in a flooded area"></div>
  <div class="abs slide slide-c" role="img" aria-label="Person pulling a cart of animals through a flooded street"></div>
  <div class="abs overlay"></div>
  <div class="abs overlay-frame"></div>
  <div class="abs overlay-title">RECOVERY</div>
  <p class="abs overlay-text">Sed ut perspiciatis unde omnis iste natus error sit voluptatem accusan tium dolorem quelau dantium</p>
  <svg class="abs" style="left:34px;top:1462px" width="20" height="40" viewBox="0 0 20 40"><path d="M17 2L3 20l14 18" fill="none" stroke="#fff" stroke-width="3"/></svg>
  <svg class="abs" style="left:1138px;top:1462px" width="20" height="40" viewBox="0 0 20 40"><path d="M3 2l14 18L3 38" fill="none" stroke="#fff" stroke-width="3"/></svg>
</section>

<section>
  <h2 class="abs section-title" style="left:0;top:1797px;width:1200px;text-align:center;font-size:29px">What We Do</h2>
  <div class="abs rule" style="left:571px;top:1851px;width:58px"></div>

  <div class="abs tile tile-img-1" style="left:0;top:1912px;width:300px" role="img" aria-label="Collapsed building after an earthquake"></div>
  <div class="abs tile tile-text" style="left:300px;top:1912px;width:300px"><span class="notch notch-left"></span><h3>Promote animal-inclusive hazard</h3><p>Promote animal-inclusive hazard mitigation, emergency preparedness and recovery</p></div>
  <div class="abs tile tile-img-2" style="left:600px;top:1912px;width:300px" role="img" aria-label="House knocked off its foundation by a storm"></div>
  <div class="abs tile tile-text" style="left:900px;top:1912px;width:300px"><span class="notch notch-left"></span><h3>Develop and maintain</h3><p>Develop and maintain a regional capability of animal emergency responders</p></div>

  <div class="abs tile tile-text" style="left:0;top:2126px;width:300px"><span class="notch notch-right"></span><h3>Provide training</h3><p>Provide training and professional development in animal disaster management</p></div>
  <div class="abs tile tile-img-3" style="left:300px;top:2126px;width:300px" role="img" aria-label="Storm-damaged buildings and debris"></div>
  <div class="abs tile tile-text" style="left:600px;top:2126px;width:300px"><span class="notch notch-right"></span><h3>Provide initial response</h3><p>Provide initial response to support to emergency services with the evacuation of animals</p></div>
  <div class="abs tile tile-img-4" style="left:900px;top:2126px;width:300px" role="img" aria-label="Toppled house among fallen trees"></div>
</section>

<section>
  <h2 class="abs section-title" style="left:99px;top:2435px;font-size:29px">How We Do It</h2>
  <div class="abs rule" style="left:99px;top:2478px;width:67px"></div>
  <ul class="abs how-list">
    <li><svg class="pointer" width="16" height="12" viewBox="0 0 16 12"><path d="M1 6h12M9 2l4 4-4 4" fill="none" stroke="#ec1f27" stroke-width="2"/></svg>We are the leading voice for all animals affected by disaster</li>
    <li><svg class="pointer" width="16" height="12" viewBox="0 0 16 12"><path d="M1 6h12M9 2l4 4-4 4" fill="none" stroke="#ec1f27" stroke-width="2"/></svg>We act to do the right thing for the animals in a disaster management context</li>
    <li><svg class="pointer" width="16" height="12" viewBox="0 0 16 12"><path d="M1 6h12M9 2l4 4-4 4" fill="none" stroke="#ec1f27" stroke-width="2"/></svg>We develop local capacity to create animal inclusive community resilience</li>
    <li><svg class="pointer" width="16" height="12" viewBox="0 0 16 12"><path d="M1 6h12M9 2l4 4-4 4" fill="none" stroke="#ec1f27" stroke-width="2"/></svg>We hold to account those with responsibilities to protect animals from disaster</li>
    <li><svg class="pointer" width="16" height="12" viewBox="0 0 16 12"><path d="M1 6h12M9 2l4 4-4 4" fill="none" stroke="#ec1f27" stroke-width="2"/></svg>We inform our position and activities using best practice and scientific knowledge</li>
    <li><svg class="pointer" width="16" height="12" viewBox="0 0 16 12"><path d="M1 6h12M9 2l4 4-4 4" fill="none" stroke="#ec1f27" stroke-width="2"/></svg>We do not advocate on non-disaster related animal welfare issues.</li>
  </ul>
  <div class="abs how-art" role="img" aria-label="Illustration of pets stranded on a rooftop in floodwater asking for help"></div>
</section>

<footer>
  <div class="abs site-footer"></div>
  <div class="abs foot-brand"><span class="foot-mark"></span><span class="foot-name">BRINDLE HAVEN.NZ</span></div>

  <h3 class="abs foot-head" style="left:527px;top:2907px">QUICK LINKS</h3>
  <div class="abs foot-rule" style="left:527px;top:2945px"></div>
  <ul class="abs foot-links" style="left:527px;top:2970px">
    <li><svg width="14" height="12" viewBox="0 0 16 12"><path d="M1 6h12M9 2l4 4-4 4" fill="none" stroke="#fff" stroke-width="2"/></svg>Home</li>
    <li><svg width="14" height="12" viewBox="0 0 16 12"><path d="M1 6h12M9 2l4 4-4 4" fill="none" stroke="#fff" stroke-width="2"/></svg>About Us</li>
    <li><svg width="14" height="12" viewBox="0 0 16 12"><path d="M1 6h12M9 2l4 4-4 4" fill="none" stroke="#fff" stroke-width="2"/></svg>Join Us</li>
    <li><svg width="14" height="12" viewBox="0 0 16 12"><path d="M1 6h12M9 2l4 4-4 4" fill="none" stroke="#fff" stroke-width="2"/></svg>Help Us</li>
  </ul>
  <ul class="abs foot-links" style="left:697px;top:2970px">
    <li><svg width="14" height="12" viewBox="0 0 16 12"><path d="M1 6h12M9 2l4 4-4 4" fill="none" stroke="#fff" stroke-width="2"/></svg>FAQs</li>
    <li><svg width="14" height="12" viewBox="0 0 16 12"><path d="M1 6h12M9 2l4 4-4 4" fill="none" stroke="#fff" stroke-width="2"/></svg>Contact Us</li>
  </ul>

  <h3 class="abs foot-head" style="left:893px;top:2907px">ADDRESS</h3>
  <div class="abs foot-rule" style="left:893px;top:2945px"></div>
  <ul class="abs foot-links" style="left:893px;top:2970px">
    <li><svg width="12" height="14" viewBox="0 0 12 16"><path d="M6 15C2 10 1 8 1 6a5 5 0 0110 0c0 2-1 4-5 9z" fill="#fff"/><circle cx="6" cy="6" r="2" fill="#222"/></svg>48 Harrowgate Lane</li>
    <li>KT4 9PL Westbury</li>
    <li>United Kingdom</li>
    <li><svg width="13" height="13" viewBox="0 0 16 16"><path d="M3 1l3 3-2 2c1 2 4 5 6 6l2-2 3 3-2 2C7 15 1 9 1 3z" fill="#fff"/></svg>Tel: +180 044 7190</li>
  </ul>

  <div class="abs foot-line"></div>
  <p class="abs copyright">Copyright © 2018 Brindle Haven. All Right Reserved.</p>
</footer>

</body>
</html>
```